Trabworth Business Cards

We need a business card design for Trabworth Mining.

This is a B2B company that buys and sells large machinery tires within the coal mining industry. The design should the strong, crisp and masculine. I have uploaded the company logo and rough mock-up of what the back of the card should look like. the front of the card should have the same look/feel as the back. I need editable templates for both the front and the back of the card.

Color scheme should be grey/green/black

Contact information to include on the card:
Name: Dale Pembrose
Title: Managing Director
Phone: 555-314-2069
Address: 1187 Welford #3 Dallas, TX 75290
Email: Dale@Trabworth-example.com

I am also opening a contest for letterhead design. If you submit a business card design, please also submit a letterhead design with the same look/feel. The winner of the business card design will also will the letter head and be paid for both.

Target Market(s)

Procurement men/women in the coal mining industry

Industry/Entity Type

Coal Mining

```html
<!DOCTYPE html>
<html lang="en">
<head>
<meta charset="utf-8">
<title>Trabworth Mining Business Card</title>
<link rel="stylesheet" href="https://fonts.googleapis.com/css2?family=Arimo:wght@400;700&display=swap">
<style>
  :root {
    --page-bg: #ffffff;
    --card-bg: #ffffff;
    --card-border: #1a1a1a;
    --ink-grey: #58595b;
    --brand-green: #62a844;
    --light-green: #b6d48e;
    --ink-white: #ffffff;
  }
  html, body {
    margin: 0;
    width: 1200px;
    height: 1000px;
    overflow: hidden;
    background: var(--page-bg);
    font-family: "Arimo", Arial, sans-serif;
  }
  .business-card {
    position: absolute;
    left: 76px;
    top: 200px;
    width: 1046px;
    height: 596px;
    background: var(--card-bg);
    border: 2px solid var(--card-border);
    box-shadow: 4px 6px 8px rgba(0, 0, 0, 0.18);
    overflow: hidden;
  }
  .divider-rule {
    position: absolute;
    left: 0;
    top: 195px;
    width: 674px;
    height: 3px;
    background: var(--brand-green);
  }
  .accent-panel-top {
    position: absolute;
    left: 674px;
    top: 0;
    width: 372px;
    height: 195px;
    background: var(--light-green);
  }
  .accent-panel-bottom {
    position: absolute;
    left: 674px;
    top: 199px;
    width: 372px;
    height: 397px;
    background: var(--brand-green);
  }
  .brand {
    position: absolute;
    left: 68px;
    top: 66px;
    display: flex;
    align-items: center;
    gap: 22px;
  }
  .brand-square {
    width: 34px;
    height: 34px;
    background: var(--brand-green);
  }
  .brand-name {
    font-weight: 700;
    font-size: 44px;
    letter-spacing: 1px;
    color: var(--ink-grey);
    text-transform: uppercase;
    line-height: 1;
  }
  .person-name {
    position: absolute;
    left: 68px;
    top: 308px;
    margin: 0;
    font-size: 34px;
    font-weight: 400;
    color: var(--ink-grey);
  }
  .person-title {
    position: absolute;
    left: 68px;
    top: 358px;
    margin: 0;
    font-size: 25px;
    color: var(--ink-grey);
  }
  .contact-direct {
    position: absolute;
    left: 68px;
    top: 482px;
    margin: 0;
    font-size: 26px;
    line-height: 36px;
    color: var(--ink-grey);
    font-style: normal;
  }
  .contact-office {
    position: absolute;
    left: 720px;
    top: 483px;
    margin: 0;
    font-size: 23px;
    line-height: 27px;
    color: var(--ink-white);
    font-style: normal;
  }
</style>
</head>
<body>
  <div class="business-card">
    <div class="accent-panel-top"></div>
    <div class="accent-panel-bottom"></div>
    <div class="divider-rule"></div>

    <div class="brand">
      <span class="brand-square"></span>
      <span class="brand-name">Trabworth Mining</span>
    </div>

    <h1 class="person-name">Dale Pembrose</h1>
    <p class="person-title">Managing Director</p>

    <address class="contact-direct">
      (555) 314-2069<br>
      Dale@Trabworth-example.com
    </address>

    <address class="contact-office">
      1187 Welford Street, #3<br>
      Dallas, TX 75290<br>
      www.trabworth-example.com
    </address>
  </div>
</body>
</html>
```